Mobile Dental services for School Students

I need a double sided letter/flyer designed to go to principals of schools about our services.
I have attached an example of a previous flyer done and would like something similar except with our other company logo and stock photos etc.

Please have a look at the word doc as this is the layout I want and the information that needs to be included on the flyer.
The colour scheme is orange, green, white, grey etc. Basically the colours of the dental truck photo.

Please see attachments as all these need to be incorporated into the flyer.

Target Market(s)

Schools, Principals

Industry/Entity Type

School

Font styles to use
Serif
Sans Serif

Colors
f37122
00a990
959595
ffffff
606060

Requirements
Must have
• Email, phone number, website, logo etc.

```html
<!DOCTYPE html>
<html lang="en">
<head>
<meta charset="utf-8">
<title>Brightway Dental – Letter to Principals</title>
<link href="https://fonts.googleapis.com/css2?family=Cabin:wght@400;700&family=Ubuntu:wght@500&family=Dancing+Script:wght@700&display=swap" rel="stylesheet">
<style>
  :root{
    --orange:#f37122;
    --teal:#00a990;
    --grey:#959595;
    --dark-grey:#606060;
    --white:#ffffff;
    --backdrop:#ececec;
    --photo-light:#7fb9cc;
    --photo-dark:#2f8fa8;
  }
  *{box-sizing:border-box;margin:0;padding:0}
  html,body{width:1200px;height:1200px;overflow:hidden}
  body{background:var(--backdrop);font-family:"Cabin",sans-serif;color:var(--dark-grey)}
  .flyer{position:absolute;left:158px;top:20px;width:883px;height:1161px;background:var(--white);overflow:hidden;box-shadow:0 6px 24px rgba(0,0,0,.12)}
  .hero{position:absolute;left:0;top:0;width:883px;height:560px}
  .brand{position:absolute;left:32px;top:42px;display:flex;align-items:center;gap:8px;font-family:"Cabin",sans-serif;font-weight:700;font-size:30px;line-height:1;color:var(--teal)}
  .brand-dot{width:14px;height:14px;border-radius:50%;background:var(--teal)}
  .headline{position:absolute;right:30px;top:52px;text-align:right;font-family:"Ubuntu",sans-serif;font-weight:500;font-size:36px;line-height:37px;color:var(--white);text-transform:uppercase}
  .letter{position:absolute;left:34px;top:557px;width:813px;font-size:13.6px;line-height:17.4px;text-align:justify}
  .letter p{margin-bottom:5.5px}
  .offers{list-style:none;margin-bottom:5.5px}
  .offers li{position:relative;padding-left:13px}
  .offers li::before{content:"";position:absolute;left:1px;top:7px;width:3px;height:3px;border-radius:50%;background:var(--teal)}
  .offers li.wrap{padding-left:0;text-indent:13px}
  .offers li.wrap::before{left:1px}
  .phone{white-space:nowrap}
  .phone svg{width:11px;height:13px;vertical-align:-2px;margin:0 3px 0 2px}
  .sign-off{position:absolute;left:34px;top:1024px;font-size:13.6px;line-height:17.4px}
  .signature{margin-top:19px;font-family:"Dancing Script",cursive;font-size:15px;line-height:16px;color:#333}
  .web{position:absolute;right:28px;top:1083px;font-size:18px;color:var(--grey)}
  .web .domain{font-size:24px;font-weight:700;color:var(--orange)}
  .web .domain span{color:var(--teal)}
  .footer-bar{position:absolute;top:1127px;height:16px}
  .footer-bar.teal{left:0;width:651px;background:var(--teal)}
  .footer-bar.orange{left:656px;right:0;background:var(--orange)}
</style>
</head>
<body>
<main class="flyer">
  <svg class="hero" viewBox="0 0 883 560" xmlns="http://www.w3.org/2000/svg">
    <defs>
      <linearGradient id="photoTone" x1="0" y1="0" x2="1" y2="1">
        <stop offset="0" stop-color="var(--photo-dark)"/>
        <stop offset="1" stop-color="var(--photo-light)"/>
      </linearGradient>
    </defs>
    <rect x="0" y="110" width="883" height="440" fill="url(#photoTone)" role="img" aria-label="Photo of a dentist in a mask examining a smiling young patient"/>
    <path d="M0,0 H883 V120 Q400,110 0,186 Z" fill="var(--white)"/>
    <path d="M115,163 Q450,55 883,0 V155 Q600,118 115,163 Z" fill="var(--orange)"/>
    <path d="M245,104 Q520,20 720,0 H800 Q520,28 245,104 Z" fill="var(--teal)"/>
    <path d="M0,401 Q260,500 640,534 Q280,522 0,442 Z" fill="var(--orange)"/>
    <path d="M0,449 Q320,538 883,540 V546 Q320,556 0,490 Z" fill="var(--teal)"/>
    <path d="M0,490 Q320,556 883,546 V560 H0 Z" fill="var(--white)"/>
  </svg>

  <div class="brand"><span class="brand-dot"></span>Brightway Dental</div>
  <h1 class="headline">Dental services<br>at your door step</h1>

  <section class="letter">
    <p>Dear Principal,</p>
    <p>We thank you for the time you are taking to review our mobile dental service.&nbsp; Here at Brightway Dental, we are committed to ‘bring the dentist to you’.</p>
    <p>We are passionate about providing Bulked billed oral health care to all types of schools.&nbsp; We also service corporate companies, rural communities and aboriginal communities.</p>
    <p>Within Victoria, in the past year, we have serviced over 150 schools, and treated a total of 22,014 students so far.</p>
    <p>We are pleased to introduce our service designed to satisfy your student’s dental needs.&nbsp; Our service is cost effective, user friendly and extremely beneficial in providing oral health education and prevention.&nbsp; We offer;</p>
    <ul class="offers">
      <li class="wrap">Free Bulked Billed and treatment to students who qualify for Medicare “CDBS” program; this includes a dental check-up, cleaning &amp; fluoride treatments, sealants, x-rays and fillings.</li>
      <li>One-on-one oral health education from our professional dental clinicians.</li>
      <li>Complimentary Dental care pack comprising of a toothbrush, toothpaste and other products.</li>
      <li>Students also go into the draw to win various prices drawn after clinic’s visit to the school.</li>
      <li>Provide a referral to the student’s regular dentist for further treatment they may require.</li>
    </ul>
    <p>Brightway Dental operates within accepted best practice models, and as such, is familiar, and without exception complies with the relevant legislation, regulations, codes and guidelines governing dentistry, including but not limited to, the dental code of conduct for Health Practitioners by the Dental Board of Australia.</p>
    <p>Our mobile dental clinics feature state-of-the-art, oral health equipment and machinery.&nbsp; Including Digital x-rays systems that feature low dose radiation, as well as Australian Approved Child Safety standard wheel chair access.&nbsp; All Brightway Dental dentists, oral therapists and hygienists are licenses with the dental board of Australia and have their working with children checks.</p>
    <p>Thank you for considering Brightway Dental, my team and I look forward to providing this free service to your school and most importantly, ‘bringing the dentist to you’.</p>
    <p>If you would like to book this service for 2018, please give me a call on <span class="phone"><svg viewBox="0 0 11 13" aria-hidden="true"><path d="M3,0.5 L5,3.5 L3.6,5 Q4.4,7.6 6.4,9 L7.8,7.8 L10.5,10 L9,12.5 Q3.5,12 1,3 Z" fill="var(--teal)"/></svg>040 218 5530</span>.</p>
  </section>

  <div class="sign-off">
    <p>Kindest Regards,</p>
    <p class="signature">Clara Benton</p>
    <p>Marketing Manager</p>
  </div>

  <p class="web">www.<span class="domain">bright<span>waydental</span></span>.com.au</p>

  <div class="footer-bar teal"></div>
  <div class="footer-bar orange"></div>
</main>
</body>
</html>
```